Business card for marketing analytics company

Need a business card for new company. I have a logo already that I want to be built into the card and should use those colours

Company is called steered by tallies
Design must bring steered by tallies to life not be a card that could be for anyone with a logo put on it.

Like the front to be fairly clean and uncluttered bringing the logo out with a suitable design on the back of the card.

The logo represents a compass and business growth so those themes along with numbers, analytics , data are appropriate.
I'm often working with creative industries so also needs to reflect the creative side of analytics rather than be very corporate looking.

Target Market(s)

Ad agency, media agency, consumer goods clients

Industry/Entity Type

Market Research

Contact Information for Business Card

Needs to include name, title, email and phone number

Colors
f78f20
f68d4d
ec1f27

Requirements
Must have
• Must bring steered by tallies to life not be a card that could be for anyone with a logo put on it.
• Logo, Correct colours
• Like a design on the back that relates to company name
• Designs for both sides
Should not have
• Please do not just submit logo and a coloured card.
• It needs to have a design element to it
• No black background
• No clear cards - needs front & back

```html
<!DOCTYPE html>
<html lang="en">
<head>
<meta charset="utf-8">
<title>Steered by Tallies — Business Card</title>
<link rel="stylesheet" href="https://fonts.googleapis.com/css2?family=Open+Sans:wght@400;500;700&display=swap">
<style>
  :root {
    --orange: #f37423;
    --red: #c01a21;
    --slate: #58636a;
    --ink: #4a4a4a;
    --paper: #ffffff;
    --paper-soft: rgba(255, 255, 255, 0.32);
    --backdrop: #e6e6e6;
  }
  * { box-sizing: border-box; margin: 0; padding: 0; }
  html, body { width: 1200px; height: 987px; overflow: hidden; }
  body {
    background: var(--backdrop);
    font-family: "Open Sans", Arial, sans-serif;
    position: relative;
  }
  .card {
    position: absolute;
    left: 293px;
    width: 615px;
    height: 351px;
    border-radius: 22px;
    overflow: hidden;
  }
  .card-front { top: 130px; background: var(--paper); }
  .card-back { top: 505px; background: var(--red); }

  .brand {
    position: absolute;
    left: 39px;
    top: 44px;
    display: flex;
    align-items: center;
    gap: 18px;
  }
  .brand-dot {
    width: 82px;
    height: 82px;
    border-radius: 50%;
    border: 4px solid var(--red);
  }
  .brand-name {
    font-size: 25px;
    font-weight: 500;
    color: var(--slate);
    line-height: 27px;
  }
  .brand-name span { display: block; }
  .brand-name span + span { padding-left: 38px; }

  .name-band {
    position: absolute;
    left: 0; top: 180px;
    width: 100%; height: 66px;
    background: var(--orange);
  }
  .name-band svg { position: absolute; inset: 0; }
  .person {
    position: absolute;
    left: 39px; top: 8px;
    color: var(--paper);
  }
  .person-name { font-size: 22px; font-weight: 700; line-height: 28px; letter-spacing: 0.2px; }
  .person-title { font-size: 16px; font-weight: 400; line-height: 22px; }

  .contacts {
    position: absolute;
    left: 39px; top: 274px;
    font-size: 15px;
    color: var(--ink);
    line-height: 24px;
  }
  .contact-line { display: flex; align-items: center; gap: 8px; }
  .contact-line svg { width: 14px; height: 14px; }
  .website-front {
    position: absolute;
    right: 31px; top: 298px;
    font-size: 15px;
    color: var(--ink);
    line-height: 24px;
  }

  .back-mark {
    position: absolute;
    left: 50%; top: 128px;
    transform: translate(-50%, -50%);
    display: flex;
    align-items: center;
    gap: 18px;
  }
  .back-dot {
    width: 64px; height: 64px;
    border-radius: 50%;
    border: 4px solid var(--paper);
  }
  .back-name {
    font-size: 34px;
    font-weight: 500;
    color: var(--paper);
    white-space: nowrap;
  }
  .tally-row {
    position: absolute;
    left: 50%; top: 196px;
    transform: translateX(-50%);
  }
  .tally-row line { stroke: var(--paper-soft); stroke-width: 3; stroke-linecap: round; }
  .website-back {
    position: absolute;
    left: 0; width: 100%; top: 290px;
    text-align: center;
    color: var(--paper);
    font-size: 15px;
    letter-spacing: 5.5px;
  }
</style>
</head>
<body>
  <section class="card card-front">
    <div class="brand">
      <div class="brand-dot"></div>
      <div class="brand-name"><span>Steered by</span><span>Tallies</span></div>
    </div>

    <div class="name-band">
      <svg width="615" height="66" viewBox="0 0 615 66" aria-hidden="true">
        <polygon points="510,0 615,0 615,66 448,66" fill="#c01a21"/>
      </svg>
      <div class="person">
        <div class="person-name">MARK ELLISON</div>
        <div class="person-title">CEO/Founder</div>
      </div>
    </div>

    <div class="contacts">
      <div class="contact-line">
        <svg viewBox="0 0 24 24" aria-hidden="true"><path fill="#f37423" d="M6.6 10.8a15.1 15.1 0 0 0 6.6 6.6l2.2-2.2a1 1 0 0 1 1-.25 11.4 11.4 0 0 0 3.6.57 1 1 0 0 1 1 1V20a1 1 0 0 1-1 1A17 17 0 0 1 3 4a1 1 0 0 1 1-1h3.5a1 1 0 0 1 1 1c0 1.25.2 2.45.57 3.6a1 1 0 0 1-.25 1z"/></svg>
        <span>555 204 7719</span>
      </div>
      <div class="contact-line">
        <svg viewBox="0 0 24 24" aria-hidden="true"><rect x="2" y="5" width="20" height="14" fill="#f37423"/><path d="M2 6l10 7.5L22 6" fill="none" stroke="#fff" stroke-width="1.6"/></svg>
        <span>mark@steeredbytallies.com</span>
      </div>
    </div>
    <div class="website-front">www.steeredbytallies.com</div>
  </section>

  <section class="card card-back">
    <div class="back-mark">
      <div class="back-dot"></div>
      <div class="back-name">Steered by Tallies</div>
    </div>

    <svg class="tally-row" width="300" height="40" viewBox="0 0 300 40" aria-hidden="true">
      <g>
        <line x1="10" y1="6" x2="10" y2="34"/><line x1="20" y1="6" x2="20" y2="34"/>
        <line x1="30" y1="6" x2="30" y2="34"/><line x1="40" y1="6" x2="40" y2="34"/>
        <line x1="2" y1="30" x2="48" y2="10"/>
      </g>
      <g transform="translate(64 0)">
        <line x1="10" y1="6" x2="10" y2="34"/><line x1="20" y1="6" x2="20" y2="34"/>
        <line x1="30" y1="6" x2="30" y2="34"/><line x1="40" y1="6" x2="40" y2="34"/>
        <line x1="2" y1="30" x2="48" y2="10"/>
      </g>
      <g transform="translate(128 0)">
        <line x1="10" y1="6" x2="10" y2="34"/><line x1="20" y1="6" x2="20" y2="34"/>
        <line x1="30" y1="6" x2="30" y2="34"/><line x1="40" y1="6" x2="40" y2="34"/>
        <line x1="2" y1="30" x2="48" y2="10"/>
      </g>
      <g transform="translate(192 0)">
        <line x1="10" y1="6" x2="10" y2="34"/><line x1="20" y1="6" x2="20" y2="34"/>
        <line x1="30" y1="6" x2="30" y2="34"/><line x1="40" y1="6" x2="40" y2="34"/>
        <line x1="2" y1="30" x2="48" y2="10"/>
      </g>
      <g transform="translate(256 0)">
        <line x1="10" y1="6" x2="10" y2="34"/><line x1="20" y1="6" x2="20" y2="34"/>
        <line x1="30" y1="6" x2="30" y2="34"/>
      </g>
    </svg>

    <div class="website-back">www.steeredbytallies.com</div>
  </section>
</body>
</html>
```